Coastal Learner Bureau business cards

Australian company about to start offering its services. We recruit international students to come to study English, vocational education and postgraduate courses in Australia. We help them find the institution and select the right city they want to come to Australia. We are a young, online oriented and supportive agency. Our clients are between 18 and 35 years old, mainly University students, young professionals or people with work experience. We provide much more information that any other agency offer. We administrate a Facebook group with more than 11.000 members that daily ask questions about general information when coming to Australia, while they are here and even after they leave the country

Target Market(s)

International students from South America, Central America and Europe

Industry/Entity Type

Student

Contact Information for Business Card

Tomas Bilbrea
Managing Director
tomas@kelvarin.com.au
www.kelvoria.com.au
+61 491058264
Melbourne, Australia

Font styles to use
Serif
Sans Serif

Colors

Designer to choose colors to be used in the design.

Requirements
Must have
• Horizontal design
• Standard business card size and shape. If font uses green or yellow colours, they will have to match the ones from the logo
Nice to have
• UPDATE: Use the contents of the green image to design one of the card sides. Use our logo in the background of that side as watermark.
• Passport image, or immigration stamps. A picture of the Yarra River (from Melbourne) would be cool as well.
Should not have
• Non-standard business card size and shape
• Not black as the background colour of any sides as we are not a VIP agency or a hight class service. We are orientes to young people and they like colours, pictures, something attractive.
• Vertical design
• NO YELLOW or BLACK AS THE BACKGROUND COLOUR OF ANY SIDE OF THE BIZ CARD

```html
<!DOCTYPE html>
<html lang="en">
<head>
<meta charset="utf-8">
<title>Coastal Learner Bureau business cards</title>
<link href="https://fonts.googleapis.com/css2?family=Roboto:wght@400;700&family=Roboto+Condensed:wght@700&display=swap" rel="stylesheet">
<style>
  :root {
    --green: #11603f;
    --green-light: #2a7a56;
    --yellow: #e3b70f;
    --white: #ffffff;
    --paper: #f4f4f2;
    --backdrop: #e6e7e5;
    --rule: rgba(255,255,255,0.35);
  }
  * { margin: 0; padding: 0; box-sizing: border-box; }
  html, body { width: 1200px; height: 886px; overflow: hidden; }
  body {
    background: var(--backdrop);
    font-family: "Roboto", Arial, sans-serif;
    position: relative;
  }
  .card {
    position: absolute;
    left: 320px;
    width: 560px;
    height: 320px;
    box-shadow: 0 10px 30px rgba(0,0,0,0.18);
    overflow: hidden;
  }
  .card--front {
    top: 90px;
    background: linear-gradient(160deg, var(--green-light) 0%, var(--green) 55%);
    display: flex;
    align-items: center;
    justify-content: center;
  }
  .card--back {
    top: 470px;
    background: var(--green);
    display: flex;
  }
  .wordmark {
    display: flex;
    align-items: center;
    gap: 10px;
    font-weight: 700;
    font-size: 40px;
    letter-spacing: 0.5px;
  }
  .wordmark--small { font-size: 32px; gap: 8px; }
  .wordmark__dot {
    width: 16px; height: 16px; border-radius: 50%;
    background: var(--yellow);
  }
  .wordmark--small .wordmark__dot { width: 13px; height: 13px; }
  .wordmark--light { color: var(--white); }
  .wordmark--dark { color: var(--green); }
  .back__side {
    width: 230px;
    height: 100%;
    background: var(--paper);
    display: flex;
    align-items: center;
    justify-content: center;
  }
  .back__body {
    position: relative;
    flex: 1;
    height: 100%;
    padding: 30px 0 0 40px;
    background: linear-gradient(160deg, var(--green-light) 0%, var(--green) 45%);
    color: var(--white);
  }
  .person__name {
    font-family: "Roboto Condensed", "Arial Narrow", sans-serif;
    font-weight: 700;
    font-size: 25px;
    color: var(--yellow);
    text-transform: uppercase;
    letter-spacing: 0.3px;
    line-height: 1;
  }
  .person__role { font-size: 15px; margin-top: 4px; }
  .divider {
    height: 1px;
    width: 210px;
    margin: 14px 0;
    background: linear-gradient(90deg, transparent, var(--rule), transparent);
  }
  .contact { list-style: none; font-size: 14px; line-height: 1.45; }
  .contact__label { color: var(--yellow); font-weight: 700; margin-right: 4px; }
  .contact__place { margin-bottom: 10px; }
  .tagline { font-weight: 700; font-size: 14px; }
  .back__stripe {
    position: absolute; top: 0; right: 0; bottom: 0;
    width: 10px; background: var(--yellow);
  }
</style>
</head>
<body>
  <section class="card card--front" aria-label="Card front">
    <div class="wordmark wordmark--light"><span>Kelvoria</span><span class="wordmark__dot"></span></div>
  </section>

  <section class="card card--back" aria-label="Card back">
    <div class="back__side">
      <div class="wordmark wordmark--dark wordmark--small"><span>Kelvoria</span><span class="wordmark__dot"></span></div>
    </div>
    <div class="back__body">
      <h1 class="person__name">Tomas Bilbrea</h1>
      <p class="person__role">Managing Director</p>
      <div class="divider"></div>
      <ul class="contact">
        <li class="contact__place">Melbourne, Australia</li>
        <li><span class="contact__label">P:</span>+61 491058264</li>
        <li><span class="contact__label">E:</span>tomas@kelvarin.com.au</li>
        <li><span class="contact__label">W:</span>www.kelvoria.com.au</li>
      </ul>
      <div class="divider"></div>
      <p class="tagline">Hacemos más por ti!</p>
      <div class="back__stripe"></div>
    </div>
  </section>
</body>
</html>
```